Business Landing Page for SEO Company

Need the landing page of the website designed - I will provide the copy, will need to include details of my company and the services offered, about us, testimonials, faq, etc., and all these elements will need to be arranged graphically on the page.

I want something similar to this: https://torvanequill.com/

Not in terms of color or theme or anything, but we offer a similar service and want to display similar information.

Th services we provide are:

Premium Links
Monthly Links Subscription
Link Insertions

Need to advertise them on the front page. Additionally need a place for testimonials, company details, etc.,

We already have logo for the website. Please use the attached file to insert the logo within the overal design.

Target Market(s)

SEO marketers and agencies

Number of Pages Required

1 page

```html
<!DOCTYPE html>
<html lang="en">
<head>
<meta charset="utf-8">
<title>Vestreon — SEO Link Building</title>
<link href="https://fonts.googleapis.com/css2?family=Montserrat:wght@500;600;700;900&family=Lato:wght@400;700&display=swap" rel="stylesheet">
<style>
:root{
  --blue:#2e89e0;
  --orange:#ff8000;
  --ink:#111111;
  --text:#666666;
  --white:#ffffff;
  --footer:#111111;
  --red:#e5262b;
}
*{box-sizing:border-box;margin:0;padding:0}
html,body{width:1200px;height:3113px;overflow:hidden}
body{font-family:"Lato",sans-serif;color:var(--text);background:var(--white);position:relative}
a{text-decoration:none;color:inherit}

.site-header{height:65px;display:flex;align-items:center;justify-content:space-between;padding:0 92px 0 88px}
.brand{font-family:"Lato",sans-serif;font-weight:700;font-size:34px;color:var(--ink);letter-spacing:.5px}
.main-nav{display:flex;gap:56px;font-size:16px;color:#222}
.main-nav .active{color:var(--blue)}

.hero{height:600px;position:relative;background:linear-gradient(135deg,#3a3d42 0%,#22262b 45%,#2d3136 70%,#1b1e22 100%);display:flex;flex-direction:column;align-items:center;justify-content:center;text-align:center;color:var(--white);padding-bottom:40px}
.hero-title{font-family:"Montserrat",sans-serif;font-weight:900;font-size:82px;letter-spacing:8px;line-height:1}
.hero-sub{font-family:Arial,sans-serif;font-size:20px;line-height:27px;margin-top:24px;width:690px}

.services{display:flex;height:374px}
.service{flex:1;color:var(--white);text-align:center;padding:50px 20px 0}
.service--blue{background:var(--blue)}
.service--orange{background:var(--orange)}
.service-icon{width:70px;height:70px;margin:0 auto}
.service h2{font-family:"Montserrat",sans-serif;font-weight:500;font-size:26px;white-space:nowrap;margin:22px 0 20px}
.service p{font-size:16px;line-height:27px;text-align:justify;text-align-last:center}

.section-title{font-family:"Montserrat",sans-serif;font-weight:900;color:var(--ink);font-size:72px;line-height:66px}
.title-bar{width:46px;height:6px;background:var(--orange);margin-top:22px}
.btn{display:inline-flex;align-items:center;justify-content:center;width:200px;height:58px;border-radius:29px;background:var(--blue);color:var(--white);font-family:"Lato",sans-serif;font-weight:700;font-size:18px}

.about{height:466px;position:relative}
.about .section-title{position:absolute;left:174px;top:92px}
.about .title-bar{position:absolute;left:174px;top:238px;margin:0}
.about-body{position:absolute;left:506px;top:92px;width:520px}
.about-body p{font-size:16px;line-height:28px;text-align:justify}
.about-body .btn{margin-top:30px}

.testimonials{height:547px;position:relative;background:linear-gradient(120deg,#efe7de 0%,#f4efea 40%,#e9e2dc 70%,#f1ece8 100%)}
.testi-head{position:absolute;left:427px;top:66px;width:640px;height:80px;border:2px solid rgba(255,255,255,.7);background:rgba(255,255,255,.35);display:flex;align-items:center;padding-left:34px}
.testi-head h2{font-family:"Montserrat",sans-serif;font-weight:900;font-size:36px;color:var(--ink)}
.testi-cards{position:absolute;left:89px;top:147px;display:flex;gap:8px}
.card{width:249px;height:270px;background:var(--white);border-radius:4px;padding:20px 13px 0;position:relative}
.card-head{display:flex;align-items:center;gap:16px}
.avatar{width:60px;height:60px;border-radius:50%;background:radial-gradient(circle at 50% 40%,#e8c2a6,#b98c70)}
.card-name{font-family:"Montserrat",sans-serif;font-weight:500;font-size:16px;color:#222}
.card p{font-size:16px;line-height:27px;margin-top:20px;text-align:justify}
.card-arrow{position:absolute;right:13px;bottom:18px}
.dots{position:absolute;top:443px;left:572px;display:flex;gap:10px}
.dots span{width:6px;height:6px;border-radius:50%;background:var(--orange)}
.dots span:first-child{background:var(--blue)}

.faq{height:640px;position:relative}
.faq .section-title{position:absolute;left:174px;top:92px}
.faq .title-bar{position:absolute;left:174px;top:172px;margin:0}
.faq-list{position:absolute;left:506px;top:97px;width:520px}
.faq-item{margin-bottom:16px}
.faq-item h3{font-family:"Lato",sans-serif;font-weight:700;font-size:16px;color:var(--ink);line-height:26px}
.faq-item p{font-size:16px;line-height:28px;padding-left:4px}
.faq-list .btn{margin-top:22px}

.site-footer{height:421px;background:var(--footer);position:relative;color:var(--white)}
.footer-brand{position:absolute;left:88px;top:64px;font-size:44px;color:var(--white)}
.footer-col{position:absolute;top:74px}
.footer-col h4{font-family:"Lato",sans-serif;font-weight:700;font-size:18px;margin-bottom:22px}
.footer-col li{list-style:none;font-size:16px;line-height:30px}
.col-links{left:417px}
.col-others{left:591px}
.col-news{left:783px;width:329px}
.news-input{display:block;width:327px;height:41px;border:1px solid #ccc;background:var(--white);color:#777;font-family:"Lato",sans-serif;font-size:15px;padding-left:16px;margin-top:-2px}
.news-btn{display:block;width:327px;height:40px;margin-top:6px;background:var(--blue);color:var(--white);border:none;font-family:"Lato",sans-serif;font-weight:700;font-size:16px}
.copyright{position:absolute;left:0;right:0;top:380px;text-align:center;font-size:14px}
</style>
</head>
<body>

<header class="site-header">
  <a class="brand" href="#">Vestreon</a>
  <nav class="main-nav">
    <a class="active" href="#">Home</a>
    <a href="#">About Us</a>
    <a href="#">Services</a>
    <a href="#">FAQ</a>
    <a href="#">Contact Us</a>
  </nav>
</header>

<section class="hero" role="img" aria-label="Dark photo of a person working at a desk with SEO icon overlays">
  <h1 class="hero-title">VESTREON</h1>
  <p class="hero-sub">Lorem ipsum dolor sit amet, consectetur adipiscing elit, sed do eiusmod tempor incididunt ut labore et dolore magna aliqua</p>
</section>

<section class="services">
  <article class="service service--blue">
    <svg class="service-icon" viewBox="0 0 70 70" fill="none" stroke="#fff" stroke-width="2">
      <rect x="20" y="8" width="14" height="10" rx="4"/><rect x="32" y="8" width="14" height="10" rx="4"/>
      <rect x="20" y="20" width="14" height="10" rx="4"/><rect x="32" y="20" width="14" height="10" rx="4"/>
      <rect x="4" y="46" width="14" height="18"/><path d="M18 50h14l8-6 14-4-20 20H18"/>
    </svg>
    <h2>Premium Links</h2>
    <p>Lorem ipsum dolor sit amet, consectetur adipiscing elit, sed do eiusmod tempor incididunt ut labore et dolore magna aliqua. Ut enim ad minim veniam, quis nostrud exercitation ullamco laboris nisi ut aliquip exapariatur.</p>
  </article>
  <article class="service service--orange">
    <svg class="service-icon" viewBox="0 0 70 70" fill="none" stroke="#fff" stroke-width="2">
      <circle cx="35" cy="35" r="14"/><circle cx="35" cy="30" r="4"/><circle cx="35" cy="40" r="5"/>
      <circle cx="35" cy="8" r="3"/><circle cx="35" cy="62" r="3"/><circle cx="8" cy="35" r="3"/><circle cx="62" cy="35" r="3"/>
      <circle cx="16" cy="16" r="3"/><circle cx="54" cy="16" r="3"/><circle cx="16" cy="54" r="3"/><circle cx="54" cy="54" r="3"/>
    </svg>
    <h2>Monthly Links Subscription</h2>
    <p>Lorem ipsum dolor sit amet, consectetur adipiscing elit, sed do eiusmod tempor incididunt ut labore et dolore magna aliqua. Ut enim ad minim veniam, quis nostrud exercitation ullamco laboris nisi ut aliquip exapariatur.</p>
  </article>
  <article class="service service--blue">
    <svg class="service-icon" viewBox="0 0 70 70" fill="none" stroke="#fff" stroke-width="2">
      <path d="M28 4h26l10 10v42H28z"/><path d="M54 4v10h10"/>
      <path d="M8 16h26l6 6v44H8z"/>
      <rect x="14" y="42" width="12" height="7" rx="3.5" transform="rotate(-45 20 45)"/>
      <rect x="20" y="36" width="12" height="7" rx="3.5" transform="rotate(-45 26 39)"/>
    </svg>
    <h2>Link Insertions</h2>
    <p>Lorem ipsum dolor sit amet, consectetur adipiscing elit, sed do eiusmod tempor incididunt ut labore et dolore magna aliqua. Ut enim ad minim veniam, quis nostrud exercitation ullamco laboris nisi ut aliquip exapariatur.</p>
  </article>
</section>

<section class="about">
  <h2 class="section-title">ABOUT<br>US</h2>
  <div class="title-bar"></div>
  <div class="about-body">
    <p>Lorem ipsum dolor sit amet, consectetur adipiscing elit, sed do eiusmod tempor incididunt ut labore et dolore magna aliqua. Ut enim ad minim veniam, quis nostrud exercitation ullamco laboris nisi ut aliquip ex ea commodo consequat. Duis aute irure dolor in reprehenderit in voluptate velit esse cillum dolore eu fugiat nulla pariatur. Excepteur sint occaecat cupidatat non proident, sunt in culpa qui officia deserunt mollit anim id est laborum</p>
    <a class="btn" href="#">Get Started</a>
  </div>
</section>

<section class="testimonials" role="img" aria-label="Soft blurred photo of hands holding a phone">
  <div class="testi-head"><h2>TESTIMONIALS</h2></div>
  <div class="testi-cards">
    <article class="card">
      <div class="card-head"><div class="avatar" role="img" aria-label="Client portrait"></div><span class="card-name">MARA DELLON</span></div>
      <p>Lorem ipsum dolor sit amet, consectetur adipiscing elit, sed do eiusmod tempor incididunt ut labore et dolore magna aliqua.</p>
      <svg class="card-arrow" width="24" height="8" viewBox="0 0 24 8"><path d="M0 4h20M17 1l4 3-4 3" stroke="var(--red)" stroke-width="1.5" fill="none"/></svg>
    </article>
    <article class="card">
      <div class="card-head"><div class="avatar" role="img" aria-label="Client portrait"></div><span class="card-name">MARA DELLON</span></div>
      <p>Lorem ipsum dolor sit amet, consectetur adipiscing elit, sed do eiusmod tempor incididunt ut labore et dolore magna aliqua.</p>
      <svg class="card-arrow" width="24" height="8" viewBox="0 0 24 8"><path d="M0 4h20M17 1l4 3-4 3" stroke="var(--red)" stroke-width="1.5" fill="none"/></svg>
    </article>
    <article class="card">
      <div class="card-head"><div class="avatar" role="img" aria-label="Client portrait"></div><span class="card-name">MARA DELLON</span></div>
      <p>Lorem ipsum dolor sit amet, consectetur adipiscing elit, sed do eiusmod tempor incididunt ut labore et dolore magna aliqua.</p>
      <svg class="card-arrow" width="24" height="8" viewBox="0 0 24 8"><path d="M0 4h20M17 1l4 3-4 3" stroke="var(--red)" stroke-width="1.5" fill="none"/></svg>
    </article>
    <article class="card">
      <div class="card-head"><div class="avatar" role="img" aria-label="Client portrait"></div><span class="card-name">MARA DELLON</span></div>
      <p>Lorem ipsum dolor sit amet, consectetur adipiscing elit, sed do eiusmod tempor incididunt ut labore et dolore magna aliqua.</p>
      <svg class="card-arrow" width="24" height="8" viewBox="0 0 24 8"><path d="M0 4h20M17 1l4 3-4 3" stroke="var(--red)" stroke-width="1.5" fill="none"/></svg>
    </article>
  </div>
  <div class="dots"><span></span><span></span><span></span><span></span></div>
</section>

<section class="faq">
  <h2 class="section-title">FAQ</h2>
  <div class="title-bar"></div>
  <div class="faq-list">
    <div class="faq-item">
      <h3>Lorem ipsum dolor sit amet, consectetur adipiscing elit?</h3>
      <p>sed do eiusmod tempor incididunt ut labore et dolore magna aliqua. Ut enim ad minim veniam, quis nostrud exercitation ullamco laboris nisi ut aliquip</p>
    </div>
    <div class="faq-item">
      <h3>Lorem ipsum dolor sit amet, consectetur adipiscing elit?</h3>
      <p>sed do eiusmod tempor incididunt ut labore et dolore magna aliqua. Ut enim ad minim veniam, quis nostrud exercitation ullamco laboris nisi ut aliquip</p>
    </div>
    <div class="faq-item">
      <h3>Lorem ipsum dolor sit amet, consectetur adipiscing elit?</h3>
      <p>sed do eiusmod tempor incididunt ut labore et dolore magna aliqua. Ut enim ad minim veniam, quis nostrud exercitation ullamco laboris nisi ut aliquip</p>
    </div>
    <a class="btn" href="#">View All</a>
  </div>
</section>

<footer class="site-footer">
  <a class="brand footer-brand" href="#">Vestreon</a>
  <div class="footer-col col-links">
    <h4>Links</h4>
    <ul><li>Home</li><li>About Us</li><li>Services</li><li>FAQ</li><li>Contact Us</li></ul>
  </div>
  <div class="footer-col col-others">
    <h4>Others</h4>
    <ul><li>Blog</li><li>Privacy Policy</li></ul>
  </div>
  <div class="footer-col col-news">
    <h4>Newsletter</h4>
    <input class="news-input" type="email" placeholder="Enter Your Email Address">
    <button class="news-btn" type="button">Subscribe</button>
  </div>
  <p class="copyright">Copyright © The Company Name 2021 &nbsp;|&nbsp; Privacy Policy Terms of Use</p>
</footer>

</body>
</html>
```